Academic and Business book cover

I need a book cover for my academic and business book.
The focus is in international / global negotiation and influence (how to negotiate across cultures).
The book will be published on Zelvorn, both in Vaspet and printed edition. therefore I need something that works under Zelvorn guidelines.The final design should be elegant and still be able to stand out against the competition.
I would like to have orange+grey for the text colors on the cover, even if different options are welcome.
Title and my name are in the attached word doc.

Target Market(s)

graduates, Phds, from international business schools. Managers

Industry/Entity Type

Business

Font styles to use
Serif
Sans Serif

Colors

Designer to choose colors to be used in the design.

Requirements
Must have
• The title and my name should have elegant fonts.
Nice to have
• pictures of the world that don't have the "usual" Europe in the centre.

```html
<!DOCTYPE html>
<html lang="en">
<head>
<meta charset="utf-8">
<title>The 4Cs Compass — Book Cover</title>
<link rel="stylesheet" href="https://fonts.googleapis.com/css2?family=Cinzel:wght@600;700&family=Marcellus+SC&display=swap">
<style>
  :root {
    --canvas-bg: #eeeeee;
    --cover-top: #56728f;
    --cover-bottom: #6f8aa6;
    --band-edge: #3a4552;
    --title-red: #e8241d;
    --light-text: #f2f4f7;
    --globe-light: #b9c0c8;
    --globe-mid: #4a525c;
    --globe-dark: #1b1f25;
  }
  * { margin: 0; padding: 0; box-sizing: border-box; }
  html, body {
    width: 1200px;
    height: 1000px;
    overflow: hidden;
    background: var(--canvas-bg);
  }
  .book-cover {
    position: absolute;
    left: 300px;
    top: 50px;
    width: 600px;
    height: 900px;
    background: linear-gradient(170deg, var(--cover-top), var(--cover-bottom));
    box-shadow: 0 6px 24px rgba(0,0,0,0.18);
    overflow: hidden;
  }
  .author-name {
    position: absolute;
    top: 56px;
    left: 0;
    width: 100%;
    text-align: center;
    font-family: "Marcellus SC", serif;
    font-size: 24px;
    letter-spacing: 1.5px;
    color: var(--light-text);
  }
  .book-title {
    position: absolute;
    top: 110px;
    left: 0;
    width: 100%;
    text-align: center;
    font-family: "Cinzel", serif;
    font-weight: 700;
    font-size: 66px;
    line-height: 72px;
    letter-spacing: 2px;
    color: var(--title-red);
    text-shadow: 1px 2px 2px rgba(0,0,0,0.25);
  }
  .cover-artwork {
    position: absolute;
    top: 290px;
    left: 0;
    width: 600px;
    height: 360px;
  }
  .book-subtitle {
    position: absolute;
    top: 690px;
    left: 0;
    width: 100%;
    text-align: center;
    font-family: "Marcellus SC", serif;
    font-size: 21px;
    line-height: 27px;
    letter-spacing: 0.5px;
    color: var(--light-text);
  }
</style>
</head>
<body>
  <main class="book-cover">
    <p class="author-name">Harlan J. Okoro</p>
    <h1 class="book-title">The 4Cs<br>Compass</h1>

    <svg class="cover-artwork" viewBox="0 0 600 360">
      <defs>
        <linearGradient id="bandFill" x1="0" y1="0" x2="1" y2="0">
          <stop offset="0" stop-color="#6d7c8d"/>
          <stop offset="0.5" stop-color="#8594a4"/>
          <stop offset="1" stop-color="#717f90"/>
        </linearGradient>
        <radialGradient id="globeFill" cx="0.62" cy="0.3" r="0.8">
          <stop offset="0" stop-color="var(--globe-light)"/>
          <stop offset="0.45" stop-color="var(--globe-mid)"/>
          <stop offset="1" stop-color="var(--globe-dark)"/>
        </radialGradient>
      </defs>
      <g class="stripe-bands">
        <line x1="100" y1="20" x2="480" y2="20" stroke="var(--band-edge)" stroke-width="1.5"/>
        <rect x="74" y="25" width="444" height="62" fill="url(#bandFill)"/>
        <line x1="100" y1="106" x2="480" y2="106" stroke="var(--band-edge)" stroke-width="1.5"/>
        <rect x="74" y="111" width="444" height="62" fill="url(#bandFill)"/>
        <line x1="100" y1="191" x2="480" y2="191" stroke="var(--band-edge)" stroke-width="1.5"/>
        <rect x="74" y="196" width="444" height="62" fill="url(#bandFill)"/>
        <line x1="100" y1="282" x2="480" y2="282" stroke="var(--band-edge)" stroke-width="1.5"/>
        <rect x="74" y="287" width="444" height="66" fill="url(#bandFill)"/>
      </g>
      <circle class="globe-illustration" cx="289" cy="184" r="158" fill="url(#globeFill)"
              role="img" aria-label="Globe with grid lines showing the Americas at its centre"/>
    </svg>

    <p class="book-subtitle">Cross-Cultural Bargaining and Persuasion<br>Methods for Worldwide Results</p>
  </main>
</body>
</html>
```